KRV Business Card

Looking for a business card for my restaurant group I own. Four different concepts:

Copperfield Alehouse
Bristow Alehouse
Tanager's Stone Hearth Kitchen
Pellston Patty Company

Card doesn't need to include all the logos.

```html
<!DOCTYPE html>
<html lang="en">
<head>
<meta charset="utf-8">
<title>KRV Business Card</title>
<link href="https://fonts.googleapis.com/css2?family=Noto+Sans:wght@400;600&display=swap" rel="stylesheet">
<style>
  :root {
    --page: #ebebeb;
    --card: #1b1a1b;
    --gold: #c9b077;
    --white: #ffffff;
    --ghost: #232223;
  }
  * { margin: 0; padding: 0; box-sizing: border-box; }
  html, body { width: 1200px; height: 800px; overflow: hidden; }
  body {
    background: var(--page);
    font-family: "Noto Sans", Arial, sans-serif;
    position: relative;
  }
  .card {
    position: absolute;
    left: 316px;
    width: 570px;
    height: 330px;
    background: var(--card);
    overflow: hidden;
  }
  .card--front { top: 50px; }
  .card--back { top: 419px; }

  .brand {
    position: absolute;
    left: 0; right: 0;
    text-align: center;
    color: var(--gold);
    font-weight: 600;
    text-transform: uppercase;
    line-height: 1.15;
  }
  .card--front .brand { top: 66px; font-size: 22px; letter-spacing: 4px; }
  .card--back .brand { top: 112px; font-size: 36px; letter-spacing: 6px; }

  .backdrop-name {
    position: absolute;
    left: 58px;
    top: 138px;
    font-size: 130px;
    font-weight: 600;
    letter-spacing: 4px;
    color: var(--ghost);
    line-height: 1;
  }

  .holder {
    position: absolute;
    left: 0;
    width: 271px;
    top: 199px;
    text-align: right;
    color: var(--gold);
    font-size: 19px;
    font-weight: 600;
  }
  .divider {
    position: absolute;
    left: 284px;
    top: 201px;
    width: 1.5px;
    height: 30px;
    background: var(--gold);
  }
  .contact {
    position: absolute;
    left: 296px;
    top: 195px;
    list-style: none;
  }
  .contact li {
    display: flex;
    align-items: center;
    gap: 9px;
    color: var(--white);
    font-size: 14px;
    height: 20px;
  }
  .contact svg { width: 12px; height: 12px; flex: none; }
  .company-line {
    position: absolute;
    left: 0; right: 0;
    top: 281px;
    text-align: center;
    color: var(--white);
    font-size: 14px;
  }
</style>
</head>
<body>
  <section class="card card--front">
    <div class="backdrop-name" aria-hidden="true">KRV</div>
    <div class="brand">Kestrel Ridge<br>Ventures</div>
    <p class="holder">Dana Whitcombe</p>
    <span class="divider"></span>
    <ul class="contact">
      <li>
        <svg viewBox="0 0 12 12" aria-hidden="true"><path d="M2.5 1h2l1 2.5-1.3 1a6 6 0 0 0 3.3 3.3l1-1.3L11 7.5v2A1.5 1.5 0 0 1 9.5 11 8.5 8.5 0 0 1 1 2.5 1.5 1.5 0 0 1 2.5 1z" fill="none" stroke="#c9b077" stroke-width="1.2"/></svg>
        555-014-2290
      </li>
      <li>
        <svg viewBox="0 0 12 12" aria-hidden="true"><rect x="1" y="2.5" width="10" height="7" fill="#c9b077"/><path d="M1.5 3l4.5 3.5L10.5 3" fill="none" stroke="#1b1a1b" stroke-width="1"/></svg>
        dana@krvrestaurants.com
      </li>
    </ul>
    <p class="company-line">Kestrel Ridge Ventures</p>
  </section>

  <section class="card card--back">
    <div class="brand">Kestrel Ridge<br>Ventures</div>
  </section>
</body>
</html>
```